Stationery Design Project for Nimbora, Chicago

Nimbora, a street parking application which helps car drivers find a street parking spot by offering an ideal path along which to look for parking. This path is calculated by our algorithm based on data (e.g. historical data, baseball games schedule, etc.). Along this path the driver will find a spot and will also save 70% of the search time. Customer we target is reg. between 21 and 45 yo.

We envision something young, fresh, bright and original. Slightly abstract maybe. It should represent the idea and elements of finding street parking in the city, e.g. car(s), parking spot, people, city, etc. (just ideas!).

Logo is attached.

Requirement:
- Business Cards (2 Sided Full Color CMYK)
- Letterhead (1 Sided Full Color CMYK)
- Envelope (1 Sided Full Color CMYK)
- Sticker (1 Sided Full Color CMYK), round with a 2inch diameter.

Reason: We're starting to get more and more designs and need more time to look into all of them. Very exciting!! Thanks to everybody!

Hi all, we're in the process of selecting our favs. Though choices!!! Really good submissions. Will keep you posted and sorry for the delay.

Target Market(s)

Car drivers and owners between 21 and 45

Industry/Entity Type

Parking

Requirements
Must have
• Sticker should be round and include company URL nimbora.com and the new logo which we will attach soon.
Should not have
• Should not be too serious or boring.

```html
<!DOCTYPE html>
<html lang="en">
<head>
<meta charset="utf-8">
<title>Nimbora Business Card</title>
<link href="https://fonts.googleapis.com/css2?family=Open+Sans:wght@400;700&display=swap" rel="stylesheet">
<style>
  :root {
    --backdrop: #d9d9d9;
    --card: #ffffff;
    --ink: #111111;
    --brand-blue: #0a72b8;
    --brand-blue-dark: #1d4f8f;
    --swoosh-dark: #2b2b2b;
    --mark-blue: #1f5fb0;
  }
  html, body {
    margin: 0;
    padding: 0;
    width: 954px;
    height: 1200px;
    overflow: hidden;
    background: var(--backdrop);
    font-family: "Open Sans", Arial, sans-serif;
  }
  .canvas {
    position: relative;
    width: 954px;
    height: 1200px;
  }
  .card {
    position: absolute;
    left: 72px;
    width: 794px;
    height: 453px;
    background: var(--card);
    border-radius: 30px;
    overflow: hidden;
    box-shadow: 0 4px 10px rgba(0,0,0,0.25);
  }
  .card--front { top: 100px; }
  .card--back { top: 648px; }
  .card__swoosh {
    position: absolute;
    top: 0;
    left: 0;
    width: 794px;
    height: 453px;
  }
  .brand {
    position: absolute;
    display: flex;
    align-items: center;
    gap: 26px;
  }
  .card--front .brand { left: 50px; top: 56px; }
  .card--back .brand { left: 112px; top: 158px; }
  .brand__dot {
    width: 156px;
    height: 156px;
    border-radius: 50%;
    background: var(--mark-blue);
    flex: none;
  }
  .brand__name {
    font-size: 92px;
    font-weight: 400;
    color: var(--ink);
    letter-spacing: 1px;
    line-height: 1;
  }
  .holder {
    position: absolute;
    left: 0;
    width: 852px;
    top: 256px;
    margin: 0;
    text-align: center;
    font-size: 24px;
    font-weight: 700;
    color: var(--ink);
  }
  .contact {
    position: absolute;
    left: 0;
    width: 832px;
    top: 362px;
    margin: 0;
    text-align: center;
    font-size: 19px;
    line-height: 26px;
    color: var(--ink);
  }
  .contact b { font-weight: 700; }
  .contact .sep { padding: 0 6px; }
</style>
</head>
<body>
<main class="canvas">
  <section class="card card--front">
    <svg class="card__swoosh" viewBox="0 0 794 453" aria-hidden="true">
      <defs>
        <linearGradient id="blueFront" x1="0" y1="0" x2="1" y2="0">
          <stop offset="0" stop-color="var(--brand-blue-dark)"/>
          <stop offset="1" stop-color="var(--brand-blue)"/>
        </linearGradient>
      </defs>
      <path d="M600 0 Q748 62 794 222 L794 0 Z" fill="url(#blueFront)"/>
      <path d="M562 0 Q740 72 794 252 L794 238 Q736 70 582 0 Z" fill="var(--swoosh-dark)"/>
    </svg>
    <div class="brand">
      <span class="brand__dot"></span>
      <span class="brand__name">nimbora</span>
    </div>
    <p class="holder">Your Name - Designation</p>
    <p class="contact">
      <b>t</b> : 123-456-7890<span class="sep">|</span><b>m</b> : 123-456-7890<br>
      <b>e</b> : name@website.com<span class="sep">|</span><b>w</b> : www.website.com
    </p>
  </section>

  <section class="card card--back">
    <svg class="card__swoosh" viewBox="0 0 794 453" aria-hidden="true">
      <defs>
        <linearGradient id="blueBack" x1="0" y1="0" x2="1" y2="0">
          <stop offset="0" stop-color="var(--brand-blue-dark)"/>
          <stop offset="1" stop-color="var(--brand-blue)"/>
        </linearGradient>
      </defs>
      <path d="M600 0 Q748 62 794 222 L794 0 Z" fill="url(#blueBack)"/>
      <path d="M562 0 Q740 72 794 252 L794 238 Q736 70 582 0 Z" fill="var(--swoosh-dark)"/>
    </svg>
    <div class="brand">
      <span class="brand__dot"></span>
      <span class="brand__name">nimbora</span>
    </div>
  </section>
</main>
</body>
</html>
```